Design NEW business card

We would like a business card using the colour deep red wine or dark navy blue textured background (patterned or not, open to suggestions) with a high gloss debossed rose gold/copper RM Roland Mercer Jewellery business name (Provided). I have included images for your review we would like to keep our currently logo and business name on the front but you can change the layout and positioning. For the back of the card we are open to all suggestions/variations.
Business
Use our current RM Roland Mercer Jewellery logo (Provided image)

```html
<!DOCTYPE html>
<html lang="en">
<head>
<meta charset="utf-8">
<title>Roland Mercer Jewellery — Business Card</title>
<link href="https://fonts.googleapis.com/css2?family=Montserrat:wght@400;500&family=Open+Sans:wght@400;600&display=swap" rel="stylesheet">
<style>
  :root {
    --backdrop: #cbae95;
    --wine: #561c23;
    --deboss: #2a080c;
    --deboss-soft: #33090f;
  }
  * { margin: 0; padding: 0; box-sizing: border-box; }
  html, body {
    width: 1200px;
    height: 1200px;
    overflow: hidden;
    background: var(--backdrop);
  }
  .canvas {
    position: relative;
    width: 1200px;
    height: 1200px;
  }
  .card {
    position: absolute;
    left: 274px;
    width: 650px;
    height: 369px;
    background: var(--wine);
  }
  .card--front { top: 185px; }
  .card--back { top: 636px; }

  .brand-mark {
    position: absolute;
    border: 2px solid var(--deboss);
    border-radius: 50%;
  }
  .card--front .brand-mark { left: 172px; top: 92px; width: 110px; height: 110px; }
  .card--back .brand-mark { left: 182px; top: 88px; width: 96px; height: 96px; }

  .brand {
    position: absolute;
    color: var(--deboss);
    font-family: "Montserrat", sans-serif;
    font-weight: 500;
    white-space: nowrap;
  }
  .card--front .brand { left: 238px; top: 222px; }
  .card--back .brand { left: 242px; top: 190px; }
  .brand__name {
    display: block;
    line-height: 1;
  }
  .card--front .brand__name { font-size: 23px; letter-spacing: 0.28em; }
  .card--back .brand__name { font-size: 19px; letter-spacing: 0.28em; }
  .brand__trade {
    display: block;
    margin-top: 12px;
    font-size: 9px;
    line-height: 1;
  }
  .card--front .brand__trade { letter-spacing: 24px; }
  .card--back .brand__trade { letter-spacing: 19px; margin-top: 10px; }

  .holder {
    position: absolute;
    left: 42px;
    top: 292px;
    font-family: "Open Sans", sans-serif;
    color: var(--deboss);
  }
  .holder__name {
    font-size: 16px;
    font-weight: 600;
    line-height: 1.2;
  }
  .holder__role {
    font-size: 13px;
    line-height: 1.35;
  }

  .contact {
    position: absolute;
    right: 50px;
    top: 268px;
    list-style: none;
    text-align: right;
    font-family: "Open Sans", sans-serif;
    font-size: 12px;
    line-height: 22px;
    color: var(--deboss-soft);
  }
</style>
</head>
<body>
  <main class="canvas">
    <section class="card card--front" aria-label="Business card front">
      <span class="brand-mark" aria-hidden="true"></span>
      <div class="brand">
        <span class="brand__name">ROLAND MERCER</span>
        <span class="brand__trade">JEWELLERY</span>
      </div>
    </section>

    <section class="card card--back" aria-label="Business card back">
      <span class="brand-mark" aria-hidden="true"></span>
      <div class="brand">
        <span class="brand__name">ROLAND MERCER</span>
        <span class="brand__trade">JEWELLERY</span>
      </div>

      <div class="holder">
        <p class="holder__name">Your Full Name</p>
        <p class="holder__role">Designation</p>
      </div>

      <ul class="contact">
        <li>(02)+ 98-765-432</li>
        <li>info@rmjewelers.com</li>
        <li>www.rmjewelers.com</li>
      </ul>
    </section>
  </main>
</body>
</html>
```